Stationery Design Project

Hi All,

We need you to design stationary for a new Business and Accounting Advisory Firm. We have already got the logo designed and it is attached. If you could also if possible, match the fonts in your design to that on the logo’s provided.

What we need:
- Business Card
- A4 Letter head
- A4 Folders
- PPT template (Title page and regular page)

And what ever else you want to throw in.

We are in the process of getting the web site designed, however below is a list of websites which we like which will give you an understanding of the style that we are going for.

- plivant.example
- moldrabay.example
- tarvenhook.example
- quillorbank.example

I look forward to your seeing your design.
Updates

Hi All,

I have just realised that I forgot that i need to include a Sworn Ledgerkeepers image on the letter head, please find attaced as File 1. Could you please have this image in the bottom left header.

Regards,

Marcus

Industry/Entity Type

Business

Requirements
Must have
• Outputs:
- Documents ready to print
- Generic editable information
- Pdf copies of the documents
- Word version of letterhead

```html
<!DOCTYPE html>
<html lang="en">
<head>
<meta charset="utf-8">
<title>Tessaly Partners – Presentation Template</title>
<link href="https://fonts.googleapis.com/css2?family=EB+Garamond:wght@500&family=Source+Sans+3:wght@300;400;700&display=swap" rel="stylesheet">
<style>
  :root {
    --board: #e3e2e3;
    --paper: #ffffff;
    --navy: #2f4e92;
    --blue-deep: #3a5a9a;
    --blue-light: #4bc1da;
    --orange: #f27c22;
    --yellow: #fdc935;
    --rule: #a9adc4;
    --white: #ffffff;
  }
  * { margin: 0; padding: 0; box-sizing: border-box; }
  html, body { width: 1200px; height: 2538px; overflow: hidden; }
  body { background: var(--board); font-family: "Source Sans 3", "Myriad Pro", sans-serif; position: relative; }

  .slide {
    position: absolute; left: 82px; width: 1037px; height: 776px;
    background: var(--paper); overflow: hidden;
    box-shadow: 6px 8px 14px rgba(0,0,0,.28);
  }
  .slide--title { top: 67px; }
  .slide--content { top: 883px; }
  .slide--closing { top: 1699px; height: 778px;
    background: linear-gradient(90deg, var(--blue-deep), var(--blue-light)); }

  .brand-name { font-family: "EB Garamond", Georgia, serif; font-weight: 500; color: var(--navy); white-space: nowrap; }
  .brand-tag { font-family: "Source Sans 3", sans-serif; color: var(--navy); text-transform: none; white-space: nowrap; }
  .brand-dot { border-radius: 50%; background: var(--orange); }

  /* Title slide */
  .title-brand { position: absolute; top: 80px; left: 0; width: 100%; text-align: center; }
  .title-brand .brand-dot { width: 84px; height: 84px; margin: 0 auto 22px; }
  .title-brand .brand-name { font-size: 50px; line-height: 1; }
  .title-brand .brand-tag { font-size: 20px; letter-spacing: 7px; margin-top: 10px; }
  .accent-band { position: absolute; top: 381px; left: 0; width: 100%; height: 54px;
    background: linear-gradient(90deg, var(--orange), var(--yellow)); }
  .hero-band { position: absolute; top: 442px; left: 0; width: 100%; bottom: 0;
    background: linear-gradient(90deg, var(--blue-deep), var(--blue-light));
    color: var(--white); text-align: center; }
  .hero-band .slide-title { font-size: 47px; font-weight: 700; margin-top: 100px; line-height: 1.2; }
  .hero-band .slide-subtitle { font-size: 44px; font-weight: 300; line-height: 1.3; }

  /* Content slide */
  .content-brand { position: absolute; top: 58px; left: 54px; display: flex; align-items: center; gap: 14px; }
  .content-brand .brand-dot { width: 64px; height: 64px; }
  .content-brand .brand-name { font-size: 32px; line-height: 1; }
  .content-brand .brand-tag { font-size: 13px; letter-spacing: 5px; margin-top: 3px; }
  .header-rule { position: absolute; top: 145px; left: 54px; width: 916px; height: 2px; background: var(--rule); }
  .content-heading { position: absolute; top: 184px; left: 56px; color: var(--navy); }
  .content-heading .slide-title { font-size: 31px; font-weight: 700; line-height: 1.35; }
  .content-heading .slide-subtitle { font-size: 30px; font-weight: 400; line-height: 1.3; }
  .footer-line { position: absolute; top: 744px; left: 0; width: 100%; height: 4px;
    background: linear-gradient(90deg, var(--orange), var(--yellow)); }
  .footer-band { position: absolute; top: 751px; left: 0; width: 100%; height: 25px;
    background: linear-gradient(90deg, var(--blue-deep), var(--blue-light)); }

  /* Closing slide */
  .closing-message { position: absolute; top: 290px; width: 100%; text-align: center;
    color: var(--white); font-size: 55px; font-weight: 700; line-height: 1.3; }
  .closing-brand { position: absolute; top: 540px; width: 100%; text-align: center; }
  .closing-brand .brand-dot { width: 66px; height: 66px; margin: 0 auto 14px; background: var(--white); }
  .closing-brand .brand-name { color: var(--white); font-size: 30px; line-height: 1; }
  .closing-brand .brand-tag { color: var(--white); font-size: 13px; letter-spacing: 5px; margin-top: 4px; }
  .contact-line { position: absolute; top: 698px; width: 100%; display: flex; justify-content: center;
    gap: 14px; color: var(--white); font-size: 12.5px; }
  .contact-item { display: flex; align-items: center; gap: 5px; }
  .contact-item svg { width: 12px; height: 12px; fill: var(--white); }
</style>
</head>
<body>

<section class="slide slide--title">
  <div class="title-brand">
    <div class="brand-dot"></div>
    <div class="brand-name">Tessaly Partners</div>
    <div class="brand-tag">Business Advisors</div>
  </div>
  <div class="accent-band"></div>
  <div class="hero-band">
    <p class="slide-title">Your&nbsp; Titles Here</p>
    <p class="slide-subtitle">Subtitle Here</p>
  </div>
</section>

<section class="slide slide--content">
  <div class="content-brand">
    <div class="brand-dot"></div>
    <div>
      <div class="brand-name">Tessaly Partners</div>
      <div class="brand-tag">Business Advisors</div>
    </div>
  </div>
  <div class="header-rule"></div>
  <div class="content-heading">
    <p class="slide-title">Your&nbsp; Titles Here</p>
    <p class="slide-subtitle">Subtitle Here</p>
  </div>
  <div class="footer-line"></div>
  <div class="footer-band"></div>
</section>

<section class="slide slide--closing">
  <p class="closing-message">Thank you very much<br>for your valuable time.</p>
  <div class="closing-brand">
    <div class="brand-dot"></div>
    <div class="brand-name">Tessaly Partners</div>
    <div class="brand-tag">Business Advisors</div>
  </div>
  <div class="contact-line">
    <span class="contact-item">
      <svg viewBox="0 0 12 12"><path d="M6 0a4 4 0 0 0-4 4c0 3 4 8 4 8s4-5 4-8a4 4 0 0 0-4-4zm0 5.5a1.5 1.5 0 1 1 0-3 1.5 1.5 0 0 1 0 3z"/></svg>
      Brinkstraat 22-C4, 4821 KL, Voorhaven
    </span>
    <span class="contact-item">
      <svg viewBox="0 0 12 12"><path d="M3 1l2 2.5-1.2 1.3a7 7 0 0 0 3.4 3.4L8.5 7 11 9l-1.3 2C5 11 1 7 1 2.3z"/></svg>
      415-555-0142
    </span>
    <span class="contact-item">
      <svg viewBox="0 0 12 12"><rect x="1" y="4" width="10" height="6" rx="1"/><rect x="3" y="1" width="6" height="3"/></svg>
      415-555-0143
    </span>
    <span class="contact-item">
      <svg viewBox="0 0 12 12"><circle cx="6" cy="6" r="6"/></svg>
      info@tessalypartners.example
    </span>
    <span class="contact-item">
      <svg viewBox="0 0 12 12"><circle cx="6" cy="6" r="6"/></svg>
      www.tessalypartners.example
    </span>
  </div>
</section>

</body>
</html>
```